New Business Cards for NYC Salon

We are updating all of our cards. 7142-8863-2095 is my account number. We put names of our stylists on their cards. The back should include appointment space. Were looking for something more sleek and modern. Black/White Silver... or even touches of the orange color on our website which has been our thing for years. The design should communicate professional upscale boutique salon for men and women. Should be able to incorporate design into thank you cards, referral cards, brochure and postcards. The file is a zip file...we like the stacked ones black or white or the side versions.

Industry/Entity Type

Beauty Salon

Contact Information for Business Card

Marcus John's Salon313 W. 53rd Street, New York NY 10019 212-683-2741 info@marcusellingsalon.example www.marcusellingsalon.example

Font styles to use
Other font styles liked:
• trajan

Requirements
Must have
• we print a different card for every person in the salon. Begin by designing with the name Marcus. We will change it with every employee when printing. Must have a space for appointment date and time.
Nice to have
• Were looking to move towards the stacked or side placed logo but not opposed to utilizing the circular.
Should not have
• Photos

```html
<!DOCTYPE html>
<html lang="en">
<head>
<meta charset="utf-8">
<title>Marcus Elling's Salon – Business Card</title>
<link rel="stylesheet" href="https://fonts.googleapis.com/css2?family=Source+Sans+3:ital,wght@0,400;0,600;1,600&display=swap">
<style>
  :root {
    --backdrop: #1b1b1c;
    --card: #333336;
    --ink: #f2f2f2;
    --rule: #8a8a8e;
    --divider: #3d3d41;
  }
  * { margin: 0; padding: 0; box-sizing: border-box; }
  html, body { width: 1200px; height: 900px; overflow: hidden; }
  body {
    position: relative;
    background: var(--backdrop);
    font-family: "Source Sans 3", sans-serif;
    color: var(--ink);
  }
  .card {
    position: absolute;
    background: var(--card);
    border-radius: 14px;
  }
  .card--front { left: 330px; top: 121px; width: 542px; height: 314px; }
  .card--back  { left: 329px; top: 484px; width: 557px; height: 323px; }

  .brand-mark {
    position: absolute;
    left: 30px; top: 110px;
    width: 195px;
    text-align: center;
    font-size: 19px;
    font-weight: 400;
    line-height: 1.4;
    letter-spacing: 0.18em;
    text-transform: uppercase;
  }
  .divider {
    position: absolute;
    left: 243px; top: 70px;
    width: 1px; height: 180px;
    background: var(--divider);
  }
  .contact { position: absolute; left: 271px; top: 64px; }
  .contact__name { font-size: 23px; font-weight: 600; line-height: 1; margin-bottom: 26px; }
  .contact__address, .contact__lines { font-size: 15px; line-height: 21px; }
  .contact__address { margin-bottom: 17px; }
  .contact__lines p { line-height: 23.5px; }

  .appointment__title {
    position: absolute; left: 0; right: 0; top: 50px;
    text-align: center; font-size: 24px; font-weight: 600; line-height: 1;
  }
  .field {
    position: absolute; font-size: 15px; line-height: 1;
  }
  .field-rule {
    position: absolute; height: 1px; background: var(--rule);
  }
  .appointment__notice {
    position: absolute; left: 0; right: 0; top: 263px;
    text-align: center; font-size: 16px; font-weight: 600; font-style: italic;
  }
</style>
</head>
<body>
  <section class="card card--front">
    <div class="brand-mark">Marcus Elling's Salon</div>
    <div class="divider"></div>
    <div class="contact">
      <h1 class="contact__name">Marcus Elling's Salon</h1>
      <p class="contact__address">742 E. 18th Street,<br>New York NY 10003</p>
      <div class="contact__lines">
        <p>T: 212-683-2741</p>
        <p>E: info@marcusellingsalon.example</p>
        <p>W: marcusellingsalon.example</p>
      </div>
    </div>
  </section>

  <section class="card card--back">
    <h2 class="appointment__title">Your Next Appointment is</h2>

    <span class="field" style="left:67px; top:116px;">Name :</span>
    <span class="field-rule" style="left:130px; top:128px; width:338px;"></span>

    <span class="field" style="left:67px; top:158px;">Date :</span>
    <span class="field-rule" style="left:124px; top:168px; width:346px;"></span>

    <span class="field" style="left:67px; top:206px;">Time:</span>
    <span class="field-rule" style="left:120px; top:217px; width:121px;"></span>
    <span class="field" style="left:248px; top:206px;">AM</span>
    <span class="field-rule" style="left:285px; top:217px; width:158px;"></span>
    <span class="field" style="left:455px; top:206px;">PM</span>

    <p class="appointment__notice">If unable to keep appointment, kindly give 24hrs notice.</p>
  </section>
</body>
</html>
```